Bath Salt Packaging

Hello! We are Dr Velmo Organics, a company providing the best and most nutritious food and health-care products for the health conscious around the world!
We are currently in the process of releasing a few new products, one of which is Himalayan Bath Salt Crystals. It is an ancient, pure salt which has been protected from environmental toxins and pollution under the Himalayan mountains for more than 250 million years!
Our salt is 100% pure and unrefined, still containing the original mineral composition of the ancient life-giving ocean that supported our early ancestors. There are over 60 trace minerals in this salt, the majority of which exist in colloidal forms, meaning they are highly bioavailable and quickly ionized when added to water.
So, we need packaging designed for our four salt packets; a 300mL jar, a 150mL jar, a 10g sachet and a box which will house the sachets. I have attached the label content, measurements and a little extra instruction/information.
We want a natural, eco-friendly feel for the packaging. Thanks!
ps. please use the 3rd of the Logo's (TM, 'Organics' under leaf)

```html
<!DOCTYPE html>
<html lang="en">
<head>
<meta charset="utf-8">
<title>Himalayan Bath Salt Crystals – Label</title>
<link rel="stylesheet" href="https://fonts.googleapis.com/css2?family=Bebas+Neue&family=Great+Vibes&family=Open+Sans:wght@700&family=Quicksand:wght@500&display=swap">
<style>
  :root {
    --leaf-green: #5ea52e;
    --forest-green: #1e4a2d;
    --ink-grey: #3a3a3a;
    --white: #ffffff;
    --wood-light: #f1efec;
    --wood-mid: #ddd8d2;
    --salt-pink: #e7b4a6;
    --bronze: #8a7350;
  }
  html, body {
    margin: 0;
    padding: 0;
    overflow: hidden;
    background: #ffffff;
  }
  .label {
    position: relative;
    width: 1078px;
    height: 1200px;
    overflow: hidden;
  }
  .backdrop {
    position: absolute;
    inset: 0;
    background:
      radial-gradient(ellipse 260px 260px at 150px 880px, #f3e2dc 0%, rgba(243,226,220,0) 100%),
      radial-gradient(ellipse 280px 220px at 960px 660px, var(--salt-pink) 0%, rgba(231,180,166,0) 100%),
      radial-gradient(ellipse 320px 300px at 880px 1000px, var(--bronze) 0%, rgba(138,115,80,0) 100%),
      radial-gradient(ellipse 300px 200px at 480px 1180px, #b57b52 0%, rgba(181,123,82,0) 100%),
      linear-gradient(180deg, var(--wood-light) 0%, #eceae6 50%, var(--wood-mid) 100%);
  }
  .natural-ribbon {
    position: absolute;
    left: 18px;
    top: 120px;
    width: 330px;
    height: 62px;
    background: var(--leaf-green);
    transform: rotate(-24deg);
    display: flex;
    align-items: center;
    justify-content: center;
    font-family: "Great Vibes", cursive;
    font-size: 46px;
    color: var(--white);
  }
  .brand-name {
    position: absolute;
    left: 0;
    right: 0;
    top: 140px;
    text-align: center;
    font-family: "Great Vibes", cursive;
    font-size: 96px;
    line-height: 1;
    color: var(--ink-grey);
  }
  .product-origin {
    position: absolute;
    left: 0;
    right: 0;
    top: 318px;
    text-align: center;
    font-family: "Great Vibes", cursive;
    font-size: 124px;
    line-height: 1;
    color: var(--leaf-green);
  }
  .product-title {
    position: absolute;
    left: 0;
    right: 0;
    top: 432px;
    margin: 0;
    text-align: center;
    font-family: "Bebas Neue", sans-serif;
    font-weight: 400;
    font-size: 134px;
    line-height: 116px;
    letter-spacing: 6px;
    color: var(--forest-green);
  }
  .values-badge {
    position: absolute;
    left: 646px;
    top: 768px;
    width: 372px;
    height: 372px;
  }
  .net-weight {
    position: absolute;
    left: 0;
    right: 0;
    top: 1098px;
    text-align: center;
    font-family: "Open Sans", sans-serif;
    font-weight: 700;
    font-size: 54px;
    line-height: 1;
    color: var(--white);
  }
</style>
</head>
<body>
<main class="label">
  <div class="backdrop" role="img" aria-label="Photo of pink Himalayan salt crystals in wooden bowls with a brass mortar and pestle on white wood"></div>

  <div class="natural-ribbon">100% Natural</div>

  <div class="brand-name">Dr Velmo Organics</div>

  <div class="product-origin">Himalayan</div>
  <h1 class="product-title">Bath Salt<br>Crystals</h1>

  <svg class="values-badge" viewBox="0 0 372 372" aria-label="Organic, Ecofriendly, Fair trading, Healthy, Sustainable">
    <defs>
      <path id="badge-ring-path" d="M186,186 m-146,0 a146,146 0 1,1 292,0 a146,146 0 1,1 -292,0"/>
    </defs>
    <circle cx="186" cy="186" r="184" fill="var(--white)"/>
    <circle cx="186" cy="186" r="178" fill="none" stroke="var(--leaf-green)" stroke-width="6"/>
    <circle cx="186" cy="186" r="118" fill="none" stroke="var(--leaf-green)" stroke-width="6"/>
    <text font-family="Quicksand, sans-serif" font-weight="500" font-size="30" fill="var(--leaf-green)" letter-spacing="1">
      <textPath href="#badge-ring-path" startOffset="2%">Sustainable • Organic • Ecofriendly • Fair trading • Healthy •</textPath>
    </text>
    <circle cx="186" cy="186" r="112" fill="#d9dcde" role="img" aria-label="Portrait photo of the company doctor in a white coat"/>
  </svg>

  <div class="net-weight">150g</div>
</main>
</body>
</html>
```